Ecological Cosmetics (w/ Social Impact) Website

Dr. Wendelin Marovitz Naturprodukte KELVORA®, a small family-run ecological cosmetics “start-up” business (has been around since the mid 90s but only now beginning professionalize management), wishes to redesign its web presence, as part of a comprehensive “facelift” that will also encompass at a later stage its corporate identity (e.g. logo…).
We would like to prepare a new trilingual (later 3 additional languages will be added) website (www.kelvora7.at) that is symbiotic with web 2.0 enabled interwoven with a blog, news section, social networks integrated (e.g. preference/like buttons, plain shape), changing images and announcements appearing on first page, online payment services, mobile internet compatibility (e.g. iOS, Android, BlackBerry… thus no use of Flash, no need for a specific app), etc. and all the other significant trends in the e-commerce realm. The website should be easily and quickly accessible, fun to navigate, allow us to update it simply (through a content manager) and so “sexy” that people will want to return to the web, inform themselves of events and news, and hopefully also try our products.
Our company is based in Austria and specializes in the production of organic cosmetics in the mid-upper pricing range. We pride ourselves in offering natural cosmetics (the meaning of “natural” is relative and each person may have a different definition), with no petrochemical preservatives. Some of our products, such as the mineral salts and black mud powder from the Dead Sea cannot be obtained more naturally, unless you actually visit the area, thus retain all their properties. Our products are not medicine but the basic Dead Sea ingredients are used by spas and clinics in the area to treat many different skin, joint and bone affections. Our male and female customers (no distinction made will be made on our new website), primarily as of the ages of 25 to 65, buy KELVORA® because they:
• Care about the exterior and interior well-being
• Wish to look well cared, preserve their skin’s flexibility, natural splendor & properties
• Prefer natural skin care
• Nourish their skin with vital minerals/trace elements, protecting/treating their skin with natural ingredients
• Willing to pay more than average for natural cosmetics, looking for quality,
• Don’t mind spending about 15 minutes per week preparing a mud mask with some hot water.
• Bathe in water enriched with mineral salts
• Know or are surprised to find out that Dead Sea mud is one of the few, if not the only, naturally astringent (tenses the skin) muds in the world
• Help alleviate skin conditions (e.g. psoriasis, dermatitis, acne, eczema, pustules, oily skin ...), joint (e.g. rheumatism, arthritis ...) and cardiovascular disease.
Amongst the minerals in many of our products (particularly salt, mud), are sulfur and zinc, two naturally disinfecting and healing minerals, thus their common use in many dermatological drugs. Both salt and mud powder are completely natural, and without chemicals additives, quite important when dealing with sensitive or problematic skin, which reacts allergically to certain types of substances. The KELVORA line blends in both ingredients, enriching them with the highest-quality vitamins, essential oils and exceptional plant oils. Many of the competitors creams today use common ingredients such as petrolatum, paraffin (paraffinum liquidum), mineral oil, among others, which are derived from oil, are cheap ingredients (higher margins!) and clog pores!
To underline that this is not a chimera, there are quite a few researchers/scientists/doctors who have written articles about the benefits of the Dead Sea and its naturally occurring substances. Below are some links to abstracts of research papers, which are helpful in understanding the therapeutic potential of the black mud powder and mineral salt:
http://onlinelibrary.wiley.com/doi/10.1111/j.1365-4362.1995.tb03599.x/abstract
http://onlinelibrary.wiley.com/doi/10.1111/j.1365-4632.2005.02079.x/full
http://onlinelibrary.wiley.com/doi/10.1046/j.1365-4362.1997.00204.x/abstract
http://ard.bmj.com/content/49/2/99.short
http://www.springerlink.com/content/pv46n2p1m9p3k131/
http://onlinelibrary.wiley.com/doi/10.1111/j.1365-4632.2005.02621.x/full
http://journals.lww.com/jclinrheum/Abstract/2002/08000/Therapy_With_Mud_Compresses_for_Knee.3.aspx
http://onlinelibrary.wiley.com/doi/10.1111/j.1468-3083.1997.tb00509.x/abstract
http://onlinelibrary.wiley.com/doi/10.1046/j.1529-8019.2003.01622.x/full
http://onlinelibrary.wiley.com/doi/10.1046/j.1365-4362.1999.00583.x/full
The following links lead you to KELVORA® product data, mineral characteristics and a video of how to prepare a facial mud mask:
http://www.kelvora7.at/descargaanalisis.htm
http://www.kelvora7.at/estudio.htm
http://www.clipverse.example/watch?v=Qm4TzLp8WxR
We would like to convey, through our striking and attractive new graphic design, our values to potential clients: quality, 100% natural product, effectiveness, seriousness, confidence, respect for the environment, people, animals (the products are not tested on animals), all of which has a price (they are not cheap!). To put our money where our mouth is and contribute to transforming our planet into a better place, we are discussing with NGOs donating a percentage of certain product sales to support their causes.
Our web currently is available in 3 languages: German, Spanish and English, however, we plan to expand it by another 2 to 3 languages (Portuguese, Russian, Chinese). We are looking for a graphic design that will communicate our values and captivate people's attention, thereby helping us increase sales, projecting a solid and elegant image of reliability, effectiveness, simplicity and trust. Although we are not, and do not wish to, market our products as medicine, we do want to express, through our new graphic design, the fact that these products can be used to treat all types of skin, mitigate certain skin affections (e.g. psoriasis, dermatitis, acne, eczema, sensitive skin), and, depending on each organism’s reaction, different ailments (e.g. arthritis, rheumatism), although they won’t cure them (they can alleviate!).
To get an idea of our company, I invite you to explore our website, www.kelvora7.at, and see photos of our products. Attached please find some photos of our products, including the newly designed black mud powder box. We would like to create a unified corporate image. At this point we know that some, if not all, packages do not convey quality nor our values – this is something we wish to gradually change as each products’ graphic design and packaging gets renewed, consistent with the new brand image. This is work-in-progress and will be addressed as the company grows and has the financial capacity to invest in new design and packaging. We are advancing step by step.
Content-wise, we would provide you with product photos, and the texts to be inserted, but would like to complement these with other photos (e.g. from photobanks that include images of the Dead Sea, beaches, plants, nature…). The design should quickly associate the Internet user/visitor of our website with our values and the idea of quality products. A content manager will be used to update and modify our product portfolio.
Although some people will find us by typing into their web browser the address of our website, many will use search engines to locate us on the WWW. For this purpose, it would also be important that kelvora7.at’s different webpages can be referenced, searched for keywords and allow analysis of webtraffic (e.g. Google Analytics…).
Two colors are being used in our packages, green Pantone No. 326 and blue Pantone No. 072. We are completely flexible in terms of colors.
We hope you find the project interesting. Any questions, please do not hesitate to contact us. Thank you very much for your time, recommendations and proposals. Ideally we can close this project in about 14 days.
Information to be considered and/or included in the design:
• The web will feature an e-commerce shop, whose design should also be included in your creative proposal.
• Cosmetics tend to be divided along the lines of skin types, yet as the KELVORA line is still quite small, we have decided to divide it along treatment areas: hair, face, body. Each product is indicated for a particular skin type.
• Keyword Search box for the entire website
The current web is slow, all in Flash, difficult to navigate, has too many intermediate stages, does not offer a keyword search function, nor incorporate any web 2.0 features. Furthermore, it is more difficult to find and index in search engines as none of the pages have specific web addresses. In terms of intermediate pages, these should be eliminated shortening the time the user needs to obtain the desired information (e.g. the landing page where you choose sex & language, followed by drop of water being filled up), such that the visitor is directly lead to the main page (equal to the landing page). At first glance, the blue background and the drop of water filling up may lead the visitor to believe we are dedicated to something with water, perhaps even plumbing or purification services – such an impression must be avoided. Perhaps one of the ways to analyze all the aspects to be incorporated is an evaluation of our current web’s weaknesses and prepare a design where those are all addressed.
Target Market(s)
Male & female customers, approx. age 18-65, who care about their exterior and interior well being, “worried” about their skin, willing to pay more tha
Industry/Entity Type
Graphic Design
Requirements
Must have
- • The web will also feature a blog and an e-commerce shop, whose designs should also be included in your creative proposal.
• Address current and future languages
Content-wise, we will product photos, and the texts to be inserted, but would like to complement these with other photos (e.g. from photobanks that include images of the Dead Sea, beaches, plants, nature…). The design should quickly associate the Internet user/visitor of our website with our values and the idea of quality products. A content manager will be used to update and modify our product portfolio, as well as effects announcements on the landing page.

```html
<!DOCTYPE html>
<html lang="en">
<head>
<meta charset="utf-8">
<title>KELVORA Naturprodukte – Blog</title>
<link href="https://fonts.googleapis.com/css2?family=Arimo:wght@400;700&family=Open+Sans:wght@400;600;700&display=swap" rel="stylesheet">
<style>
:root{
  --ink:#222;
  --bar:#252525;
  --teal:#1d9a9a;
  --navy:#1a2f8c;
  --sky-top:#cfe3e7;
  --sky-bottom:#6b8a96;
  --card:#ffffff;
  --muted:#9a9a9a;
  --link-red:#d8452c;
  --feed-blue:#1a8fc9;
  --white:#ffffff;
}
*{margin:0;padding:0;box-sizing:border-box}
html,body{width:960px;height:1200px;overflow:hidden}
body{position:relative;font-family:"Arimo",Arial,sans-serif;color:var(--ink);
  background:linear-gradient(to bottom,#fff 0,#fff 440px,var(--sky-top) 500px,#b4cdd3 760px,var(--sky-bottom) 1117px)}
.abs{position:absolute}

/* language tab */
.lang-tab{left:839px;top:0;width:97px;height:35px;background:var(--bar);border-radius:0 0 8px 8px;display:flex;gap:7px;padding:9px 0 0 5px}
.flag{width:24px;height:15px;display:block}

/* header */
.brand-mark{left:12px;top:36px;width:113px;height:113px;border-radius:50%;background:var(--navy);border:4px solid var(--white);box-shadow:0 2px 6px rgba(0,0,0,.35);z-index:2}
.header-bar{left:123px;top:61px;width:813px;height:66px;background:var(--bar);box-shadow:0 6px 10px rgba(0,0,0,.25)}
.brand-name{left:137px;top:88px;font:400 13px "Arimo",Arial,sans-serif;color:var(--teal);letter-spacing:.3px}
.main-nav{left:373px;top:89px;display:flex;font-size:12px;color:var(--white);white-space:nowrap}
.main-nav .sep{padding:0 15px;color:var(--white)}

/* hero */
.hero-products{left:38px;top:205px;width:338px;height:210px;border-radius:40px 40px 10px 10px;
  background:radial-gradient(ellipse at 50% 45%,#2fb2ad 0,#5ec7c2 40%,rgba(200,235,235,.6) 75%,rgba(255,255,255,0) 100%)}
.hero-portrait{left:405px;top:144px;width:530px;height:340px;
  background:radial-gradient(ellipse at 45% 55%,#d7a07e 0,#e6bc9d 45%,rgba(240,215,200,.4) 80%,rgba(255,255,255,0) 100%)}
.hero-curve{left:0;top:430px;z-index:1}

/* search */
.search{left:787px;top:493px;width:159px;height:22px;background:var(--white);border:1px solid #c4d2d6;border-radius:3px}
.search svg{position:absolute;left:6px;top:4px}

.section-label{left:36px;top:527px;font-size:13px;color:#6d6d6d}

/* blog cards */
.post{background:var(--card);border-radius:8px}
.post-1{left:30px;top:547px;width:617px;height:281px}
.post-2{left:30px;top:836px;width:617px;height:216px}
.post-title{position:absolute;left:17px;top:26px;font:700 12.5px "Open Sans",sans-serif;letter-spacing:.2px}
.post-meta{position:absolute;left:17px;top:51px;font-size:10.5px;color:var(--navy)}
.post-meta span{margin-right:11px}
.post-body{position:absolute;left:17px;font-size:10px;line-height:15.4px;color:#333;text-align:justify}
.post-more{position:absolute;font-size:11px;color:var(--navy)}
.post-thumb{position:absolute;left:448px;top:76px;width:132px;height:96px;
  background:radial-gradient(ellipse at 50% 60%,#b9a48a 0,#d8cdbd 50%,rgba(255,255,255,0) 85%)}

.pager{left:366px;top:1074px;font-size:11.5px;color:#f0f4f5;word-spacing:2px}

/* sidebar */
.feed-box{left:661px;top:546px;width:287px;height:316px;background:#f2f2f2;border-radius:8px}
.feed-head{position:absolute;left:0;top:10px;width:100%;height:24px}
.feed-title{position:absolute;left:96px;top:14px;font:700 12.5px "Open Sans",sans-serif;color:var(--feed-blue)}
.feed-item{position:absolute;left:20px;width:260px}
.feed-photo{position:absolute;left:0;top:0;width:91px;height:117px;background:linear-gradient(to right,#c8a690,#e8cfc0 50%,#b89482)}
.feed-text{position:absolute;left:130px;top:-3px;font:400 11px/21px "Open Sans",sans-serif;color:var(--muted);width:140px;white-space:nowrap}
.feed-text a{color:var(--link-red);text-decoration:none}

.comments-title{left:671px;top:890px;font:700 12.5px "Open Sans",sans-serif;color:var(--white)}
.comment{left:677px;width:250px;font-size:10px;line-height:15.4px;color:var(--white);padding-left:19px}
.comment svg{position:absolute;left:0;top:4px}

/* footer */
.footer{left:0;top:1117px;width:960px;height:83px;background:var(--bar)}
.foot-nav{left:24px;top:1155px;font-size:12px;color:var(--white);display:flex;white-space:nowrap}
.foot-nav .sep{padding:0 15px;color:var(--white)}
.social{left:678px;top:1151px;display:flex;gap:4px}
.social i{display:block;width:22px;height:22px;background:#555;border-radius:3px}
.payments{left:796px;top:1154px;display:flex;gap:3px}
.payments i{display:block;height:15px;background:#6a6a6a;border-radius:2px}
.copyright{left:700px;top:1182px;font-size:9.5px;color:#8c8c8c}
</style>
</head>
<body>

<div class="abs lang-tab">
  <svg class="flag" viewBox="0 0 24 15" role="img" aria-label="English"><rect width="24" height="15" fill="#233e8b"/><path d="M0 0L24 15M24 0L0 15" stroke="#fff" stroke-width="3"/><path d="M12 0V15M0 7.5H24" stroke="#fff" stroke-width="5"/><path d="M12 0V15M0 7.5H24" stroke="#c8202f" stroke-width="3"/></svg>
  <svg class="flag" viewBox="0 0 24 15" role="img" aria-label="Deutsch"><rect width="24" height="5" fill="#111"/><rect y="5" width="24" height="5" fill="#d00"/><rect y="10" width="24" height="5" fill="#fc0"/></svg>
  <svg class="flag" viewBox="0 0 24 15" role="img" aria-label="Español"><rect width="24" height="15" fill="#c60b1e"/><rect y="4" width="24" height="7" fill="#ffc400"/></svg>
</div>

<div class="abs header-bar"></div>
<div class="abs brand-mark" aria-hidden="true"></div>
<div class="abs brand-name">KELVORA NATURPRODUKTE</div>
<nav class="abs main-nav">
  <span>HOME</span><span class="sep">|</span><span>ABOUT US</span><span class="sep">|</span><span>PRODUCTS</span><span class="sep">|</span><span>SERVICES</span><span class="sep">|</span><span>DOWNLOADS</span><span class="sep">|</span><span>CONTACT US</span>
</nav>

<div class="abs hero-products" role="img" aria-label="Three teal cream jars of the KELVORA line"></div>
<div class="abs hero-portrait" role="img" aria-label="Woman resting on her arms with a pink lotus flower"></div>
<svg class="abs hero-curve" width="960" height="70" viewBox="0 0 960 70" aria-hidden="true">
  <path d="M0 20 Q480 95 960 25 L960 70 L0 70Z" fill="#cfe3e7"/>
  <path d="M0 20 Q480 95 960 25" fill="none" stroke="#fff" stroke-width="4" opacity=".9"/>
</svg>

<div class="abs search">
  <svg width="12" height="12" viewBox="0 0 12 12"><circle cx="5" cy="5" r="3.6" fill="none" stroke="#333" stroke-width="1.6"/><path d="M7.6 7.6L11 11" stroke="#333" stroke-width="1.8"/></svg>
</div>

<div class="abs section-label">BLOG</div>

<article class="abs post post-1">
  <h2 class="post-title">EXCEPTEUR SINT OCCAECAT CUPIDATAT NON PROIDEN</h2>
  <p class="post-meta"><span>Posted by : Marla</span><span>Posted on : March 10th</span><span>5.24 pm</span></p>
  <p class="post-body" style="top:80px;width:583px">Consectetuer adipiscing elit, sed diam nonummy nibh euismod tincidunt ut laoreet dolore magna aliquam erat volutpat. Ut wisi enim ad minim veniam, quis nostrud exerci tation ullamcorper suscipit lobortis nisl ut aliquip ex ea commodo consequat. Duis autem vel eum iriure dolor in hendrerit in vulputate velit esse molestie consequat,</p>
  <p class="post-body" style="top:142px;width:583px">vel illum dolore eu feugiat nulla facilisis at vero eros et accumsan et iusto odio dignissim qui blandit praesent luptatum zzril delenit augue duis dolore te feugait nulla facilisi. Nam liber tempor cum soluta nobis eleifend option congue nihil imperdiet doming id quod mazim placerat facer possim assum. Typi non habent claritatem insitam; est usus legentis in iis qui facit eorum claritatem. Investigationes demonstraverunt lectores legere me lius quod ii legunt saepius. Claritas est etiam processus dynamicus, qui sequitur mutationem consuetudium lectorum. Mirum est notare quam littera gothica, quam nunc putamus parum claram, anteposuerit litterarum formas humanitatis per seacula quarta decima et quinta decima. Eodem modo typi, qui nunc nobis videntur parum clari, fiant sollemnes in futurum.</p>
  <a class="post-more" style="left:553px;top:255px">View more</a>
</article>

<article class="abs post post-2">
  <h2 class="post-title">EXCEPTEUR SINT OCCAECAT CUPIDATAT NON PROIDEN</h2>
  <p class="post-meta"><span>Posted by : Marla</span><span>Posted on : March 10th</span><span>5.24 pm</span></p>
  <p class="post-body" style="top:80px;width:398px">Nam liber tempor cum soluta nobis eleifend option congue nihil imperdiet doming id quod mazim placerat facer possim assum. Typi non habent claritatem insitam; est usus legentis in iis qui facit eorum claritatem. Investigationes demonstraverunt lectores legere me lius quod ii legunt saepius. Claritas est etiam processus dynamicus, qui sequitur mutationem consuetudium lectorum. Mirum est notare quam littera gothica, quam nunc putamus parum claram, anteposuerit litterarum formas humanitatis per seacula quarta decima et quinta decima.</p>
  <div class="post-thumb" role="img" aria-label="Assorted natural cosmetic bottles and jars"></div>
  <a class="post-more" style="left:364px;top:195px">View more</a>
</article>

<div class="abs pager">Prvious &lt;&lt; &nbsp; 1 &nbsp; 2 &nbsp; 3 &nbsp; . . . . . &nbsp;8 &nbsp; 9 &nbsp; 10 &nbsp; &gt;&gt; Next</div>

<aside class="abs feed-box">
  <svg class="feed-head" viewBox="0 0 287 24" aria-hidden="true">
    <path d="M20 12H9M13 7L8 12L13 17" fill="none" stroke="#333" stroke-width="2"/>
    <path d="M267 12H278M274 7L279 12L274 17" fill="none" stroke="#333" stroke-width="2"/>
    <circle cx="74" cy="13" r="6" fill="var(--feed-blue)"/>
  </svg>
  <div class="feed-title">CHIRPLINE FEEDS</div>
  <div class="feed-item" style="top:45px">
    <div class="feed-photo" role="img" aria-label="Portrait photo of a woman"></div>
    <p class="feed-text">The first release in a<br>series of themes that will<br>be available on the<br>Theme Grove - Lumin<br>PressLeaf Theme<br><a>http://lnk.example/ihfm3L</a></p>
  </div>
  <div class="feed-item" style="top:181px">
    <div class="feed-photo" role="img" aria-label="Portrait photo of a woman"></div>
    <p class="feed-text">The first release in a<br>series of themes that will<br>be available on the<br>Theme Grove - Lumin<br>PressLeaf Theme<br><a>http://lnk.example/ihfm3L</a></p>
  </div>
</aside>

<h3 class="abs comments-title">RECENT COMMENTS</h3>
<div class="abs comment" style="top:921px">
  <svg width="11" height="8" viewBox="0 0 11 8"><path d="M0 4H9M6 1L9.5 4L6 7" fill="none" stroke="#fff" stroke-width="1.5"/></svg>
  Consectetuer adipiscing elit, sed diam nonummy nibh euismod tincidunt ut laoreet dolore magna aliquam erat volutpat.
</div>
<div class="abs comment" style="top:980px">
  <svg width="11" height="8" viewBox="0 0 11 8"><path d="M0 4H9M6 1L9.5 4L6 7" fill="none" stroke="#fff" stroke-width="1.5"/></svg>
  Consectetuer adipiscing elit, sed diam nonummy nibh euismod tincidunt ut laoreet dolore magna aliquam erat volutpat.
</div>

<footer class="abs footer"></footer>
<nav class="abs foot-nav">
  <span>HOME</span><span class="sep">|</span><span>ABOUT US</span><span class="sep">|</span><span>PRODUCTS</span><span class="sep">|</span><span>SERVICES</span><span class="sep">|</span><span>DOWNLOADS</span><span class="sep">|</span><span>CONTACT US</span>
</nav>
<div class="abs social" aria-label="Social links"><i></i><i></i><i></i><i></i></div>
<div class="abs payments" aria-label="Payment options"><i style="width:52px"></i><i style="width:26px"></i><i style="width:24px"></i></div>
<div class="abs copyright">Copyright © 2012. All Rights are Reserved</div>

</body>
</html>
```